New Business Card for Web Design/Internet Marketing Company

Looking for a great looking new business card. We are a 10 year old web design, internet marketing and website management company that works mostly with small businesses.

Our new card needs to better match the colors and style of our website, be bold, extremely usable and slightly edgy.

Target Market(s)

Small/Medium businesses that have websites

Industry/Entity Type

Internet

Requirements
Must have
• Front and back design, full color, rounded corners please

Must use the colors/style of our website (JPG provided)

INFO FOR CARDS (as readable as possible please)
Mark Lenner
President/CEO
mark@trelvanmedia.example
Phone: 520-381-7459
Toll Free: 866-381-7459
Address: 4315 W. Calloway Ave. Ste. 140, Tucson, AZ 85792

THINGS I WANT TO PROMOTE (if there is room):
1. Our Website - www.trelvanmedia.example

2. Social Media
Twitter: @trelvanmedia
Facebook: www.facebook.com/trelvanmedia

3. Our Services
Web Design
Internet Marketing
Website Management

```html
<!DOCTYPE html>
<html lang="en">
<head>
<meta charset="utf-8">
<title>Trelvan Media – Business Card</title>
<link href="https://fonts.googleapis.com/css2?family=Source+Sans+3:wght@400;600;700&display=swap" rel="stylesheet">
<style>
  :root {
    --brand-blue: #0f8ccf;
    --back-blue: #1a94d2;
    --brand-orange: #f28a2e;
    --ink: #4a4a4a;
    --rule: #9a9a9a;
    --white: #ffffff;
    --stage: #e8e3dc;
    --faint: rgba(255,255,255,0.12);
  }
  * { box-sizing: border-box; margin: 0; padding: 0; }
  html, body { width: 1200px; height: 402px; overflow: hidden; }
  body {
    background: var(--stage);
    font-family: "Source Sans 3", "Myriad Pro", Arial, sans-serif;
    position: relative;
  }
  .card { position: absolute; top: 59px; height: 292px; overflow: hidden; border-radius: 4px; }

  /* Front */
  .card--front { left: 62px; width: 548px; background: var(--white); }
  .brand-mark { position: absolute; top: 50px; left: 0; width: 100%; display: flex; justify-content: center; align-items: center; gap: 12px; }
  .brand-mark__dot { width: 30px; height: 30px; border-radius: 50%; background: var(--brand-blue); }
  .brand-mark__name { font-size: 44px; font-weight: 700; color: var(--brand-orange); letter-spacing: -0.5px; line-height: 1; }
  .holder { position: absolute; top: 173px; width: 100%; text-align: center; color: var(--brand-blue); }
  .holder__name { font-size: 18px; font-weight: 700; }
  .holder__title { font-size: 13px; font-weight: 400; }
  .address { position: absolute; top: 202px; width: 100%; text-align: center; font-size: 13px; color: var(--ink); }
  .divider { position: absolute; top: 231px; left: 50px; width: 425px; height: 1px; background: var(--rule); }
  .contacts { position: absolute; top: 238px; left: 110px; display: flex; }
  .contacts__col { display: flex; flex-direction: column; gap: 3px; font-size: 13px; color: var(--ink); padding: 0 12px; }
  .contacts__col + .contacts__col { border-left: 1px solid var(--rule); }
  .contact { display: flex; align-items: center; gap: 5px; line-height: 17px; }
  .contact svg { width: 10px; height: 10px; flex: none; }
  .front-band { position: absolute; bottom: 0; left: 0; width: 100%; height: 14px; }

  /* Back */
  .card--back { left: 626px; width: 512px; background: var(--back-blue); color: var(--white); }
  .back-halo { position: absolute; left: 40px; top: 10px; width: 420px; height: 300px; border-radius: 50%; background: var(--faint); }
  .back-name { position: absolute; top: 70px; width: 100%; text-align: center; font-size: 46px; font-weight: 700; line-height: 1; }
  .services { position: absolute; top: 156px; width: 100%; text-align: center; }
  .services__heading { display: inline-block; font-size: 22px; font-weight: 600; padding: 0 14px 3px; border-bottom: 2px solid var(--white); }
  .services__list { margin-top: 10px; font-size: 19px; line-height: 25px; }
  .social { position: absolute; top: 268px; width: 100%; display: flex; justify-content: center; gap: 38px; font-size: 13px; }
  .social__item { display: flex; align-items: center; gap: 4px; }
  .social__square { width: 12px; height: 12px; background: rgba(255,255,255,0.85); border-radius: 2px; }
</style>
</head>
<body>

<section class="card card--front" aria-label="Card front">
  <div class="brand-mark">
    <span class="brand-mark__dot"></span>
    <span class="brand-mark__name">trelvanmedia</span>
  </div>
  <p class="holder"><span class="holder__name">Mark Lenner,</span> <span class="holder__title">President/CEO</span></p>
  <p class="address">4315 W. Calloway Ave. Ste. 140, Tucson, AZ 85792</p>
  <div class="divider"></div>
  <div class="contacts">
    <div class="contacts__col">
      <span class="contact"><svg viewBox="0 0 10 10"><circle cx="5" cy="5" r="5" fill="#0f8ccf"/><path d="M3 2.5c0 2.5 2 4.5 4.5 4.5l.5-1-1.3-.6-.5.5c-.8-.4-1.4-1-1.8-1.8l.5-.5L4.3 2z" fill="#fff"/></svg>520-381-7459</span>
      <span class="contact"><svg viewBox="0 0 10 10"><circle cx="5" cy="5" r="5" fill="#0f8ccf"/><path d="M3 2.5c0 2.5 2 4.5 4.5 4.5l.5-1-1.3-.6-.5.5c-.8-.4-1.4-1-1.8-1.8l.5-.5L4.3 2z" fill="#fff"/></svg>866-381-7459</span>
    </div>
    <div class="contacts__col">
      <span class="contact"><svg viewBox="0 0 10 10"><rect x="0" y="2" width="10" height="7" rx="1" fill="#0f8ccf"/><path d="M0.5 2.5L5 6l4.5-3.5" stroke="#fff" stroke-width="0.8" fill="none"/></svg>mark@trelvanmedia.example</span>
      <span class="contact"><svg viewBox="0 0 10 10"><circle cx="5" cy="5" r="4.4" stroke="#0f8ccf" stroke-width="1" fill="none"/><ellipse cx="5" cy="5" rx="2" ry="4.4" stroke="#0f8ccf" stroke-width="0.8" fill="none"/><path d="M0.6 5h8.8" stroke="#0f8ccf" stroke-width="0.8"/></svg>www.trelvanmedia.example</span>
    </div>
  </div>
  <svg class="front-band" viewBox="0 0 548 14" preserveAspectRatio="none" aria-hidden="true">
    <polygon points="0,0 268,0 254,14 0,14" fill="var(--brand-orange)"/>
    <polygon points="272,0 548,0 548,14 258,14" fill="var(--brand-blue)"/>
  </svg>
</section>

<section class="card card--back" aria-label="Card back">
  <div class="back-halo"></div>
  <p class="back-name">trelvanmedia</p>
  <div class="services">
    <h2 class="services__heading">Our Services</h2>
    <p class="services__list">Web Design &nbsp;•&nbsp; Internet Marketing<br>Website Management</p>
  </div>
  <div class="social">
    <span class="social__item"><span class="social__square"></span>@trelvanmedia</span>
    <span class="social__item"><span class="social__square"></span>trelvanmedia</span>
  </div>
</section>

</body>
</html>
```